Vorlanta PowerPoint Template

I have a company called Vorlanta, LLC and my company logo is already designed. I need a PowerPoint template that I will be using to pitch potential investors and business partners. This should be a very professional-looking template that leverages the company logo colors and really pops. The company is an AI product research and development company.

```html
<!DOCTYPE html>
<html lang="en">
<head>
<meta charset="utf-8">
<title>Vorlanta – Pitch Template Overview</title>
<link href="https://fonts.googleapis.com/css2?family=Poppins:wght@400;500;600;700;800&display=swap" rel="stylesheet">
<style>
  :root{
    --ink:#000;
    --red:#c8283a;
    --red-bright:#e3252f;
    --plum:#3b1344;
    --wine:#7a1d3e;
    --magenta:#e0105a;
    --white:#fff;
    --frame:#b9b9b9;
    --grey:#9a9a9a;
    --brand-grad:linear-gradient(90deg,var(--plum),var(--red));
  }
  *{box-sizing:border-box;margin:0;padding:0}
  html,body{width:1200px;height:1184px;overflow:hidden;background:var(--ink)}
  body{position:relative;font-family:"Poppins",sans-serif;color:var(--white)}

  .masthead{position:absolute;left:0;top:55px;width:1200px;height:91px;display:flex;align-items:center;justify-content:center;gap:22px}
  .masthead-dot{width:91px;height:91px;border-radius:50%;background:var(--red)}
  .masthead-name{font-size:86px;font-weight:700;color:var(--red);letter-spacing:-3px;line-height:1}

  .slide{position:absolute;width:383px;height:215px;background:var(--ink);border:1px solid var(--frame);overflow:hidden}
  .s1{left:17px;top:212px}.s2{left:410px;top:212px}.s3{left:803px;top:212px}
  .s4{left:17px;top:440px}.s5{left:410px;top:440px}.s6{left:803px;top:440px}
  .s7{left:17px;top:671px}.s8{left:410px;top:671px}.s9{left:803px;top:671px}
  .s10{left:410px;top:902px}

  .abs{position:absolute}
  .brand{position:absolute;left:30px;top:14px;display:flex;align-items:center;gap:4px;font-size:10px;font-weight:600;color:var(--white);z-index:3}
  .brand-dot{width:11px;height:11px;border-radius:50%;background:var(--red-bright)}

  .title{position:absolute;font-weight:800;font-size:22px;line-height:1.08;letter-spacing:-.2px;z-index:2}
  .body{position:absolute;font-size:5px;line-height:1.75;color:#e8e8e8;z-index:2}
  .caps{position:absolute;font-size:4.6px;letter-spacing:2.2px;text-transform:uppercase;line-height:1.8;z-index:2}
  .card{position:absolute;background:var(--brand-grad);border-radius:7px;font-size:5px;line-height:1.75;color:#f2f2f2;padding:9px 13px;z-index:2}

  .photo{position:absolute;border-radius:4px}
  .robot{position:absolute;border-radius:45% 45% 20% 20%;background:radial-gradient(ellipse at 50% 30%,#f4f4f4 0%,#cfcfcf 45%,#6a6a6a 100%);z-index:1}
  .orb{position:absolute;border-radius:50%;background:radial-gradient(circle at 35% 35%,var(--red-bright),var(--plum));z-index:2}
  .speck{position:absolute;width:5px;height:5px;border-radius:50%;background:#5a1a6a;z-index:2}
  .pin{position:absolute;width:5px;height:5px;border-radius:50%;background:var(--red);z-index:2}

  /* slide 1 */
  .s1 .sweep{left:-118px;top:-188px;width:436px;height:436px;border-radius:50%;background:linear-gradient(90deg,var(--plum),var(--red))}
  .s1 .brand{left:35px;top:34px;font-size:25px;gap:7px}
  .s1 .brand-dot{width:30px;height:30px}
  .s1 .title{left:35px;top:84px;font-size:19.5px;line-height:1.15}
  .corner-mark{position:absolute;right:24px;top:18px;width:8px;height:8px;border:1.5px solid var(--white);border-radius:2px}

  /* slide 3 */
  .s3 .halo{left:228px;top:8px;width:330px;height:330px;border-radius:50%;background:linear-gradient(200deg,var(--wine),var(--plum))}

  /* slide 5 */
  .s5 .panel{left:174px;top:0;width:209px;height:215px;background:var(--brand-grad)}
  .s5 .year{font-weight:700;color:var(--white)}
  .s5 .rule{left:222px;top:132px;width:130px;height:1px;background:#d9a0a8;z-index:2}

  /* slide 6 */
  .s6 .halo{left:234px;top:11px;width:218px;height:218px;border-radius:50%;background:radial-gradient(circle at 60% 50%,var(--magenta),#b0083a)}

  /* slide 9 */
  .contact{position:absolute;left:37px;top:95px;width:202px;height:73px;border-radius:20px;background:var(--brand-grad);display:grid;grid-template-columns:1fr 1fr;padding:15px 20px 0;row-gap:9px;z-index:2}
  .contact dt{font-size:5px;font-weight:700}
  .contact dd{font-size:5px;margin-top:2px}
  .device{position:absolute;left:268px;top:33px;width:66px;height:135px;border:2px solid var(--white);border-radius:9px;padding:3px;z-index:2}
  .device .screen{width:100%;height:100%;border-radius:6px;background:linear-gradient(160deg,#3a1a7a,#8a2ac0 55%,#e8e8f4)}

  /* slide 10 */
  .s10 .halo{left:205px;top:35px;width:330px;height:330px;border-radius:50%;background:linear-gradient(200deg,var(--wine),var(--plum))}
  .s10 .title{font-size:27px}
</style>
</head>
<body>

<header class="masthead">
  <span class="masthead-dot"></span>
  <span class="masthead-name">Vorlanta</span>
</header>

<!-- Cover -->
<section class="slide s1">
  <div class="abs sweep"></div>
  <span class="corner-mark"></span>
  <div class="brand"><span class="brand-dot"></span>Vorlanta</div>
  <h1 class="title">AI PRODUCT<br>RESEARCH AND<br>DEVELOPMENT</h1>
  <p class="caps" style="left:35px;top:157px;">AI product research and<br>development company.</p>
  <div class="robot" role="img" aria-label="White humanoid robot giving a thumbs up" style="left:237px;top:52px;width:128px;height:170px;"></div>
  <span class="orb" style="left:340px;top:60px;width:14px;height:14px;"></span>
  <span class="speck" style="left:326px;top:114px;"></span>
</section>

<!-- Welcome -->
<section class="slide s2">
  <div class="brand"><span class="brand-dot"></span>Vorlanta</div>
  <span class="corner-mark" style="background:#5a2aa0;border-color:#5a2aa0;"></span>
  <div class="photo" role="img" aria-label="Researcher in a hard hat and safety glasses against a red backdrop" style="left:30px;top:43px;width:73px;height:122px;background:linear-gradient(160deg,#c4283a,#6a1030 60%,#e8d8e0);"></div>
  <div class="photo" role="img" aria-label="Woman holding a tablet in a dark room with floating particles" style="left:114px;top:43px;width:57px;height:122px;background:linear-gradient(180deg,#2a1020,#6a2030 60%,#3a1018);"></div>
  <h2 class="title" style="left:190px;top:50px;">Welcome to the<br>AI product<br>research</h2>
  <p class="body" style="left:189px;top:125px;width:150px;">Lorem ipsum dolor sit amet, consectetur adipiscing elit. Sed at ipsum vitae lacus lobortis lacinia. Donec tristique arcu massa, at pharetra tortor feugiat non. Etiam vehicula hendrerit aliquet.</p>
  <span class="pin" style="left:191px;top:182px;"></span>
  <span class="orb" style="left:282px;top:176px;width:14px;height:14px;"></span>
</section>

<!-- Introduction -->
<section class="slide s3">
  <div class="abs halo"></div>
  <div class="brand"><span class="brand-dot"></span>Vorlanta</div>
  <h2 class="title" style="left:37px;top:66px;">Introduction</h2>
  <p class="body" style="left:37px;top:94px;width:148px;">Lorem ipsum dolor sit amet, consectetur adipiscing elit. Sed at ipsum vitae lacus lobortis lacinia. Donec tristique arcu massa, at pharetra tortor feugiat non. Etiam vehicula hendrerit aliquet.</p>
  <div class="robot" role="img" aria-label="White humanoid robot giving a thumbs up" style="left:203px;top:24px;width:124px;height:140px;"></div>
  <p class="card" style="left:155px;top:159px;width:181px;height:46px;">Lorem ipsum dolor sit amet, consectetur adipiscing elit. Sed at ipsum vitae lacus lobortis lacinia. Donec tristique arcu massa, at pharetra tortor feugiat non.</p>
</section>

<!-- About Us -->
<section class="slide s4">
  <div class="photo" role="img" aria-label="Close-up of a glowing blue digital eye with circuitry" style="left:32px;top:0;width:142px;height:161px;border-radius:0 0 4px 4px;background:radial-gradient(circle at 60% 45%,#3aa8f0,#0a3a7a 55%,#020a20);"></div>
  <div class="brand" style="left:31px;top:14px;"><span class="brand-dot"></span>Vorlanta</div>
  <h2 class="title" style="left:190px;top:47px;">About Us</h2>
  <span class="orb" style="left:308px;top:39px;width:14px;height:14px;background:radial-gradient(circle at 35% 35%,#7a2ad0,#2a0a40);"></span>
  <p class="body" style="left:187px;top:73px;width:148px;">Lorem ipsum dolor sit amet, consectetur adipiscing elit. Sed at ipsum vitae lacus lobortis lacinia. Donec tristique arcu massa, at pharetra tortor feugiat non.</p>
  <p class="card" style="left:154px;top:114px;width:181px;height:56px;padding-top:14px;">Lorem ipsum dolor sit amet, consectetur adipiscing elit. Sed at ipsum vitae lacus lobortis lacinia. Donec tristique arcu massa, at pharetra tortor feugiat non.</p>
  <span class="speck" style="left:134px;top:174px;"></span>
</section>

<!-- Our History -->
<section class="slide s5">
  <div class="abs panel"></div>
  <div class="brand" style="left:28px;"><span class="brand-dot"></span>Vorlanta</div>
  <h2 class="title" style="left:28px;top:42px;">Our<br>History</h2>
  <span class="orb" style="left:103px;top:40px;width:14px;height:14px;"></span>
  <span class="pin" style="left:149px;top:82px;"></span>
  <div class="photo" role="img" aria-label="Hands on a keyboard beneath a glowing holographic AI interface" style="left:0;top:111px;width:196px;height:104px;border-radius:0 4px 0 0;background:radial-gradient(circle at 55% 55%,#1a6aa0,#0a1a30 60%,#02060c);z-index:2;"></div>
  <p class="body" style="left:195px;top:47px;width:158px;">Lorem ipsum dolor sit amet, consectetur adipiscing elit. Sed at ipsum vitae lacus lobortis lacinia. Donec tristique arcu massa, at pharetra tortor feugiat non.</p>
  <p class="body" style="left:222px;top:87px;width:130px;"><span class="year">2024</span><br>Lorem ipsum dolor sit amet, consectetur adipiscing elit. Sed at ipsum vitae lacus lobortis lacinia. Donec tristique arcu massa, at.</p>
  <span class="abs rule"></span>
  <p class="body" style="left:222px;top:142px;width:130px;"><span class="year">2025</span><br>Lorem ipsum dolor sit amet, consectetur adipiscing elit. Sed at ipsum vitae lacus lobortis lacinia. Donec tristique arcu massa, at.</p>
</section>

<!-- Our Vision -->
<section class="slide s6">
  <div class="abs halo" role="img" aria-label="Blurred figure in magenta light"></div>
  <div class="brand"><span class="brand-dot"></span>Vorlanta</div>
  <h2 class="title" style="left:30px;top:52px;">Our Vision</h2>
  <p class="body" style="left:30px;top:79px;width:148px;">Lorem ipsum dolor sit amet, consectetur adipiscing elit. Sed at ipsum vitae lacus lobortis lacinia. Donec tristique arcu massa, at pharetra tortor feugiat non. Etiam vehicula hendrerit aliquet.</p>
  <span class="orb" style="left:133px;top:133px;width:15px;height:15px;"></span>
  <span class="pin" style="left:49px;top:166px;"></span>
  <div class="robot" role="img" aria-label="White humanoid robot giving a thumbs up" style="left:175px;top:97px;width:96px;height:122px;"></div>
</section>

<!-- Our Mission -->
<section class="slide s7">
  <div class="photo" role="img" aria-label="Woman in a red hoodie looking at her phone among glowing red network nodes" style="left:0;top:0;width:159px;height:215px;border-radius:0;background:radial-gradient(circle at 55% 40%,#8a3a30,#4a1414 50%,#120606);"></div>
  <div class="brand"><span class="brand-dot"></span>Vorlanta</div>
  <h2 class="title" style="left:183px;top:52px;">Our Mission</h2>
  <p class="body" style="left:182px;top:79px;width:148px;">Lorem ipsum dolor sit amet, consectetur adipiscing elit. Sed at ipsum vitae lacus lobortis lacinia. Donec tristique arcu massa, at pharetra tortor feugiat non. Etiam vehicula hendrerit aliquet.</p>
  <p class="card" style="left:99px;top:128px;width:151px;height:45px;">Lorem ipsum dolor sit amet, consectetur adipiscing elit. Sed at ipsum vitae lacus lobortis lacinia. Donec tristique arcu massa, at.</p>
  <span class="orb" style="left:278px;top:147px;width:14px;height:14px;"></span>
</section>

<!-- Latest Portfolio -->
<section class="slide s8">
  <div class="brand" style="left:31px;"><span class="brand-dot"></span>Vorlanta</div>
  <span class="speck" style="left:315px;top:21px;"></span>
  <div class="photo" role="img" aria-label="Person in a VR headset touching a holographic interface" style="left:31px;top:38px;width:113px;height:65px;background:linear-gradient(135deg,#5a3ac0,#c04ad0 55%,#2a1a6a);"></div>
  <div class="photo" role="img" aria-label="Circuit board with a glowing AI chip" style="left:158px;top:38px;width:68px;height:138px;background:radial-gradient(circle at 45% 55%,#d05030,#1a2a4a 45%,#050a18);"></div>
  <div class="photo" role="img" aria-label="Developer working at multiple monitors in a dark office" style="left:240px;top:115px;width:113px;height:62px;background:linear-gradient(135deg,#1a2a3a,#3a6a7a 50%,#101820);"></div>
  <p class="card" style="left:208px;top:48px;width:145px;height:56px;padding-top:11px;">Lorem ipsum dolor sit amet, consectetur adipiscing elit. Sed at ipsum vitae lacus lobortis lacinia. Donec tristique arcu massa, at pharetra tortor feugiat non.</p>
  <h2 class="title" style="left:31px;top:117px;">Latest<br>Portfolio</h2>
  <span class="orb" style="left:129px;top:117px;width:14px;height:14px;background:radial-gradient(circle at 35% 35%,#7a2ad0,#2a0a40);"></span>
</section>

<!-- Get in Touch -->
<section class="slide s9">
  <div class="brand"><span class="brand-dot"></span>Vorlanta</div>
  <h2 class="title" style="left:37px;top:45px;">Get in Touch</h2>
  <span class="pin" style="left:207px;top:47px;"></span>
  <p class="body" style="left:37px;top:70px;width:180px;">Lorem ipsum dolor sit amet, consectetur adipiscing elit. Sed at ipsum vitae lacus lobortis lacinia. Donec tristique arcu massa, at.</p>
  <dl class="contact">
    <div><dt>Phone Number</dt><dd>+123-555-0148</dd></div>
    <div><dt>Email</dt><dd>hello@vorlanta.com</dd></div>
    <div><dt>Website</dt><dd>www.vorlanta.com</dd></div>
    <div><dt>Social Media</dt><dd>@vorlanta.ai</dd></div>
  </dl>
  <div class="device"><div class="screen" role="img" aria-label="Phone screen showing a robot head in violet light"></div></div>
  <span class="orb" style="left:197px;top:176px;width:14px;height:14px;"></span>
</section>

<!-- Thank You -->
<section class="slide s10">
  <div class="abs halo"></div>
  <div class="brand" style="left:31px;"><span class="brand-dot"></span>Vorlanta</div>
  <h2 class="title" style="left:34px;top:56px;">THANK YOU</h2>
  <p class="caps" style="left:35px;top:88px;">For your attention</p>
  <p class="body" style="left:35px;top:112px;width:160px;">Lorem ipsum dolor sit amet, consectetur adipiscing elit. Sed at ipsum vitae lacus lobortis lacinia. Donec tristique arcu massa, at.</p>
  <span class="orb" style="left:215px;top:52px;width:18px;height:18px;background:var(--ink);border:1px solid #2a1a3a;"></span>
  <span class="speck" style="left:136px;top:166px;"></span>
  <div class="robot" role="img" aria-label="White humanoid robot giving a thumbs up" style="left:220px;top:33px;width:143px;height:190px;"></div>
</section>

</body>
</html>
```